Velk Partners Building Business Cards

We need a business card that reflects our business as "Solar Experts" in San Diego. Browse our website www.velkpartners.example our License needs to be displayed as "CSLB# 3867140" our phone number is (619) 555-0187

Save thousands on your electric bills and increase the value of your home while helping to protect the environment. Our solar installation experts will help you design the system that's right for you, using only the highest quality equipment that will look great and give you ideal performance. Our goal is to make you energy independent, and get your electric bill to 0.

Paul Osterby
(619) 555-0187
paul@velkpartners.example

Target Market(s)

Home owners in san diego looking for solar

Industry/Entity Type

Solar Energy

Contact Information for Business Card

Paul Osterby
(619) 555-0187
paul@velkpartners.example

Font styles to use
Other font styles liked:
• Use our logo font

Requirements
Must have
• License needs to be displayed as "CSLB# 3867140" our phone number is (619) 555-0187
Nice to have
• Real images of rooftop home solar in san diego
Should not have
• our business address

```html
<!DOCTYPE html>
<html lang="en">
<head>
<meta charset="utf-8">
<title>Velk Partners Building – Business Cards</title>
<link href="https://fonts.googleapis.com/css2?family=Arimo:wght@400;700&display=swap" rel="stylesheet">
<style>
  :root {
    --navy: #2b4b8c;
    --sun: #f6ab00;
    --paper: #ffffff;
    --ink-grey: #555a63;
    --backdrop: #e9eaec;
  }
  * { margin: 0; padding: 0; box-sizing: border-box; }
  html, body {
    width: 1200px; height: 950px; overflow: hidden;
    background: var(--backdrop);
    font-family: "Arimo", Arial, sans-serif;
  }
  .sheet { position: relative; width: 1200px; height: 950px; }
  .card {
    position: absolute; left: 250px; width: 700px; height: 400px;
    border-radius: 4px; overflow: hidden;
    box-shadow: 0 6px 18px rgba(0,0,0,.18);
  }
  .card--front { top: 50px; background: var(--paper); }
  .card--back { top: 500px; background: var(--sun); }

  .swoosh { position: absolute; inset: 0; width: 700px; height: 400px; }

  .wordmark {
    font-weight: 700; color: var(--navy); line-height: 1.05;
    display: flex; align-items: center; gap: 12px;
  }
  .wordmark__dot { width: 18px; height: 18px; border-radius: 50%; background: var(--sun); flex: none; }

  .card--front .wordmark { position: absolute; left: 44px; top: 48px; font-size: 34px; }
  .divider { position: absolute; left: 44px; top: 130px; width: 500px; height: 1px; background: var(--navy); }
  .license { position: absolute; right: 40px; top: 56px; font-size: 15px; color: var(--ink-grey); letter-spacing: .5px; }

  .person { position: absolute; left: 44px; top: 250px; }
  .person__name { font-size: 22px; color: var(--navy); }
  .person__role { font-size: 15px; color: var(--sun); margin-top: 4px; }
  .contacts { position: absolute; left: 44px; top: 312px; list-style: none; font-size: 14px; color: var(--ink-grey); }
  .contacts li { display: flex; align-items: center; gap: 10px; height: 22px; }
  .contacts svg { width: 14px; height: 14px; fill: var(--navy); }

  .card--back .wordmark { position: absolute; left: 0; right: 0; top: 150px; justify-content: center; font-size: 46px; }
  .back-url {
    position: absolute; left: 28px; top: 200px; transform-origin: 0 0; transform: rotate(-90deg) translate(-50%, 0);
    font-size: 13px; letter-spacing: 5px; color: var(--navy);
  }
</style>
</head>
<body>
<main class="sheet">
  <section class="card card--front">
    <svg class="swoosh" viewBox="0 0 700 400" aria-hidden="true">
      <path d="M700 60 C650 170 560 330 340 400 L700 400 Z" fill="var(--navy)"/>
      <path d="M678 20 C630 150 530 320 300 400" fill="none" stroke="var(--sun)" stroke-width="9"/>
    </svg>
    <div class="wordmark"><span class="wordmark__dot"></span>Velk Partners Building</div>
    <div class="divider"></div>
    <div class="license">CSLB# 3867140</div>
    <div class="person">
      <div class="person__name">Paul Osterby</div>
      <div class="person__role">CEO/Founder</div>
    </div>
    <ul class="contacts">
      <li><svg viewBox="0 0 24 24"><path d="M6.6 10.8a15 15 0 0 0 6.6 6.6l2.2-2.2c.3-.3.7-.4 1-.2 1.1.4 2.3.6 3.6.6.6 0 1 .4 1 1V20c0 .6-.4 1-1 1A17 17 0 0 1 3 4c0-.6.4-1 1-1h3.5c.6 0 1 .4 1 1 0 1.3.2 2.5.6 3.6.1.3 0 .7-.2 1z"/></svg>(619) 555-0187</li>
      <li><svg viewBox="0 0 24 24"><path d="M2 5h20v14H2z M2 5l10 8 10-8" fill="none" stroke="var(--navy)" stroke-width="2.4"/></svg>paul@velkpartners.example</li>
      <li><svg viewBox="0 0 24 24"><circle cx="12" cy="12" r="10"/></svg>www.velkpartners.example</li>
    </ul>
  </section>

  <section class="card card--back">
    <div class="wordmark"><span class="wordmark__dot" style="background:var(--navy)"></span>Velk Partners Building</div>
    <div class="back-url">www.velkpartners.example</div>
  </section>
</main>
</body>
</html>
```